RW Framewell Inc Business cards

We need business cards using our existing logo but slightly modified. Right now the logo says RW Loadbearing Masonry. We want to keep the RW part of the design, but replace the Structural Concrete portion with "FRAMEWELL". Please see the attached file.
Ideally this would be a blank template so we can add Different Names, titles, and phone numbers later.
On the one side we want only the logo and on the other side the detail. I'm attaching an example for you to see.
Please reach out with any other questions. Our address and other details will be given out once we find a design we like.

Target Market(s)

Construction Industry

```html
<!DOCTYPE html>
<html lang="en">
<head>
<meta charset="utf-8">
<title>RW Framewell Inc — Business Cards</title>
<link href="https://fonts.googleapis.com/css2?family=Archivo+Black&family=Roboto:wght@400&display=swap" rel="stylesheet">
<style>
  :root {
    --backdrop: #b8b8b8;
    --brand-blue: #1b75bc;
    --brand-grey: #808184;
    --card-white: #ffffff;
    --shadow: #2a2a2a;
  }
  html, body {
    margin: 0;
    padding: 0;
    width: 1200px;
    height: 801px;
    overflow: hidden;
    background: var(--backdrop);
  }
  .stage {
    position: relative;
    width: 1200px;
    height: 801px;
  }
  .card {
    position: absolute;
    top: 274px;
    width: 443px;
    height: 263px;
    background: var(--card-white);
    box-shadow: 2px 2px 0 var(--shadow);
    overflow: hidden;
  }
  .card--details { left: 153px; }
  .card--logo { left: 625px; }

  .details-panel {
    position: absolute;
    left: 0;
    top: 0;
    width: 198px;
    height: 100%;
    background: var(--brand-blue);
    color: var(--card-white);
  }
  .person-name {
    position: absolute;
    left: 21px;
    top: 89px;
    margin: 0;
    font-family: "Archivo Black", sans-serif;
    font-size: 16.5px;
    letter-spacing: 0.3px;
    line-height: 1;
  }
  .person-title {
    position: absolute;
    left: 21px;
    top: 108px;
    margin: 0;
    font-family: "Roboto", sans-serif;
    font-size: 13.5px;
    line-height: 1.2;
  }
  .contact-list {
    position: absolute;
    left: 21px;
    top: 134px;
    margin: 0;
    padding: 0;
    list-style: none;
    font-family: "Roboto", sans-serif;
    font-size: 13.5px;
    line-height: 16.5px;
  }
  .contact-list li {
    display: flex;
    align-items: center;
    gap: 4px;
  }
  .contact-icon {
    width: 13px;
    height: 13px;
    flex: none;
  }

  .accent-area {
    position: absolute;
    left: 198px;
    top: 0;
    width: 245px;
    height: 100%;
    display: flex;
    align-items: center;
    justify-content: center;
  }
  .accent-mark {
    margin: 0;
    font-family: "Archivo Black", sans-serif;
    font-size: 150px;
    line-height: 1;
    color: var(--brand-grey);
  }

  .brand-name {
    position: absolute;
    left: 0;
    top: 44px;
    width: 100%;
    margin: 0;
    text-align: center;
    font-family: "Archivo Black", sans-serif;
    color: var(--brand-blue);
    line-height: 1;
  }
  .brand-name__initials {
    display: block;
    font-size: 140px;
    letter-spacing: 4px;
  }
  .brand-name__word {
    display: block;
    margin-top: -6px;
    font-size: 30px;
    letter-spacing: 2px;
  }
</style>
</head>
<body>
<main class="stage">

  <section class="card card--details" aria-label="Business card, details side">
    <div class="details-panel">
      <p class="person-name">DANIEL REYES</p>
      <p class="person-title">Managing Director</p>
      <ul class="contact-list">
        <li>
          <svg class="contact-icon" viewBox="0 0 16 16" aria-hidden="true">
            <path d="M3.5 1.5l2.5 0 1 3.5-1.8 1.2a8 8 0 0 0 4.6 4.6L11 9l3.5 1v2.5c0 1-1 2-2 2A11 11 0 0 1 1.5 3.5c0-1 1-2 2-2z" fill="none" stroke="#fff" stroke-width="1.4"/>
          </svg>
          044-987 654 321
        </li>
        <li>
          <svg class="contact-icon" viewBox="0 0 16 16" aria-hidden="true">
            <rect x="1" y="3" width="14" height="10" fill="#fff"/>
            <path d="M1 3l7 6 7-6M1 13l5.5-5M15 13l-5.5-5" fill="none" stroke="#1b75bc" stroke-width="1.1"/>
          </svg>
          info@rwframe.com
        </li>
        <li>
          <svg class="contact-icon" viewBox="0 0 16 16" aria-hidden="true">
            <g fill="none" stroke="#fff" stroke-width="1.2">
              <circle cx="8" cy="8" r="6.5"/>
              <ellipse cx="8" cy="8" rx="3" ry="6.5"/>
              <path d="M1.5 8h13M2.5 4.8h11M2.5 11.2h11M8 1.5v13"/>
            </g>
          </svg>
          www.rwframewell.com
        </li>
      </ul>
    </div>
    <div class="accent-area">
      <p class="accent-mark">RW</p>
    </div>
  </section>

  <section class="card card--logo" aria-label="Business card, logo side">
    <p class="brand-name">
      <span class="brand-name__initials">RW</span>
      <span class="brand-name__word">FRAMEWELL</span>
    </p>
  </section>

</main>
</body>
</html>
```